Brovanek Data Yellow rose letterhead

I have a new logo for my company but in its current form it is too large to be used on letterhead or as a email signature. I need to have the designer use elements from the current logo and create something close to the original but more suited for smaller items.
Updates

I just uploaded a copy of our logo that does not have the weathered affect. Thanks

Reason: More time for revisions

Industry/Entity Type

It Company

Requirements
Must have
• The design must maintain the visual effect of the current logo. It needs to include the yellow rose and the name of the company.
Nice to have
• It would be nice to maintain the stamp theme and incorporate my name, address, phone, email. etc.

```html
<!DOCTYPE html>
<html lang="en">
<head>
<meta charset="utf-8">
<title>Brovanek Data Letterhead</title>
<link rel="stylesheet" href="https://fonts.googleapis.com/css2?family=Catamaran:wght@700;800&display=swap">
<style>
  :root {
    --teal: #36b9bf;
    --ink: #3b2a25;
    --paper: #ffffff;
  }
  html, body {
    margin: 0;
    padding: 0;
    overflow: hidden;
    background: var(--paper);
  }
  .letterhead {
    position: relative;
    width: 917px;
    height: 1200px;
    overflow: hidden;
    background: var(--paper);
    font-family: "Catamaran", sans-serif;
    color: var(--ink);
  }
  .header-band,
  .footer-band {
    position: absolute;
    display: block;
  }
  .header-band {
    left: 0;
    top: 0;
    width: 700px;
    height: 181px;
  }
  .footer-band {
    right: 0;
    bottom: 0;
    width: 258px;
    height: 61px;
  }
  .brand {
    position: absolute;
    left: 708px;
    top: 66px;
    width: 190px;
    display: flex;
    align-items: center;
    gap: 10px;
  }
  .brand-square {
    width: 18px;
    height: 18px;
    background: var(--teal);
    flex: none;
  }
  .brand-name {
    font-size: 25px;
    font-weight: 800;
    line-height: 1.05;
    color: var(--ink);
  }
  .contact-line {
    position: absolute;
    left: 25px;
    top: 1164px;
    margin: 0;
    font-size: 13.5px;
    font-weight: 700;
    line-height: 1;
    white-space: nowrap;
  }
  .contact-line span {
    position: absolute;
    top: 0;
  }
  .contact-address { left: 0; }
  .contact-email { left: 339px; }
  .contact-phone { left: 528px; }
</style>
</head>
<body>
  <main class="letterhead">
    <svg class="header-band" viewBox="0 0 700 181" aria-hidden="true">
      <polygon points="0,0 694,0 627,181 0,181" fill="var(--teal)"/>
    </svg>

    <div class="brand">
      <span class="brand-square"></span>
      <span class="brand-name">Brovanek Data</span>
    </div>

    <p class="contact-line">
      <span class="contact-address">214 W Juniper Rd, Ste 118 Marlow Falls, OK 73055</span>
      <span class="contact-email">mara@brovanek-data.com</span>
      <span class="contact-phone">1-800-555-0147</span>
    </p>

    <svg class="footer-band" viewBox="0 0 258 61" aria-hidden="true">
      <polygon points="53,0 258,0 258,61 0,61" fill="var(--teal)"/>
    </svg>
  </main>
</body>
</html>
```